Luxury Business Card Design for High-End Window Treatments

Gilded Slatworks
Custom Plantation Shutters & Architectural Shading Systems

⸻

BACK

Daniel Trevick
Owner

Custom Interior & Exterior Window Treatments

919-555-0148
gildedslatworks.com

I have included a picture that I’m hoping we can use on the back, but I’m also wondering if you can get rid of the ladder? Should we get rid of shutters , shades and blinds underneath Gilded Slatworks?

Target Market(s)

High-end residential homeowners, custom home builders, architects, interior designers, and luxury renovation clients seeking premium plantation shutters and motorized architectural shading systems.

Industry/Entity Type

Custom Window treatments

Contact Information for Business Card

Front Gilded Slatworks Custom Plantation Shutters Motorized Architectural Shading Systems BACK Daniel Trevick Owner 919-555-0148 GildedSlatworks.com Custom Interior & Exterior Window Treatments By Appointment

Requirements
Nice to have
• Not 100% sure on nice to halves or the color but you can definitely check out my website to get a better understanding of what I’m trying to do

```html
<!DOCTYPE html>
<html lang="en">
<head>
<meta charset="UTF-8">
<title>Gilded Slatworks Business Card</title>
<link href="https://fonts.googleapis.com/css2?family=Andada+Pro:wght@400;600&display=swap" rel="stylesheet">
<style>
  :root {
    --backdrop: #6a6a6d;
    --card-black: #111111;
    --cream: #ece6d8;
    --gold: #f7dc6f;
    --band: #fbe36e;
    --ink: #0c0c0c;
    --white: #f2f2f2;
  }
  * { margin: 0; padding: 0; box-sizing: border-box; }
  html, body {
    width: 900px; height: 1200px; overflow: hidden;
    background: var(--backdrop);
    font-family: "Andada Pro", Georgia, serif;
  }
  .canvas { position: relative; width: 900px; height: 1200px; }

  .card {
    position: absolute; left: 135px; width: 630px; height: 358px;
    background: var(--card-black); overflow: hidden;
  }
  .card-front { top: 214px; }
  .card-back { top: 628px; }

  .front-photo {
    position: absolute; inset: 0;
    background: linear-gradient(180deg, #2a2a2a 0%, #1c1c1c 45%, #222 75%, #2d2d2d 100%);
  }
  .front-brand {
    position: absolute; left: 0; right: 0; top: 78px;
    text-align: center; color: var(--cream);
    font-size: 66px; line-height: 76px; font-weight: 400;
  }
  .front-services {
    position: absolute; left: 20px; right: 20px; top: 250px;
    text-align: center; color: var(--gold);
    font-size: 17px; line-height: 24px; font-weight: 400;
  }

  .back-brand {
    position: absolute; left: 36px; width: 284px; top: 96px;
    text-align: center; color: var(--cream);
    font-size: 50px; line-height: 58px; font-weight: 400;
  }
  .back-services {
    position: absolute; left: 36px; width: 284px; top: 238px;
    text-align: center; color: var(--gold); font-size: 21px; word-spacing: 10px;
  }
  .divider {
    position: absolute; left: 332px; top: 76px; width: 2px; height: 207px;
    background: var(--white);
  }
  .contact { position: absolute; left: 357px; top: 116px; color: var(--white); }
  .contact-name { color: var(--gold); font-size: 24px; line-height: 28px; font-weight: 400; }
  .contact-role { font-size: 14px; letter-spacing: 1.5px; margin-top: 3px; }
  .contact-rule { width: 48px; height: 2px; background: var(--gold); margin: 6px 0 14px; }
  .contact-line { font-size: 14px; line-height: 26px; letter-spacing: 0.6px; display: flex; align-items: center; gap: 6px; }
  .contact-phone { letter-spacing: 3px; }
  .icon { width: 12px; height: 12px; flex: none; }

  .appointment-band {
    position: absolute; left: 0; right: 0; top: 305px; height: 30px;
    background: var(--band); color: var(--ink);
    font-size: 17px; font-weight: 600; text-align: center; line-height: 30px;
  }
</style>
</head>
<body>
<main class="canvas">
  <section class="card card-front">
    <div class="front-photo" role="img" aria-label="Dark photograph of a covered porch with exterior shades and columns"></div>
    <h1 class="front-brand">Gilded<br>Slatworks</h1>
    <p class="front-services">Custom Plantation Shutters &amp; Motorized Architectural Shading Systems</p>
  </section>

  <section class="card card-back">
    <h2 class="back-brand">Gilded<br>Slatworks</h2>
    <p class="back-services">Shutters Shades Blinds</p>
    <div class="divider"></div>
    <div class="contact">
      <p class="contact-name">Daniel Trevick</p>
      <p class="contact-role">Owner</p>
      <div class="contact-rule"></div>
      <p class="contact-line contact-phone">
        <svg class="icon" viewBox="0 0 24 24"><path fill="#f7dc6f" d="M6.6 10.8a15 15 0 0 0 6.6 6.6l2.2-2.2a1 1 0 0 1 1-.25 11.4 11.4 0 0 0 3.6.57 1 1 0 0 1 1 1V20a1 1 0 0 1-1 1A17 17 0 0 1 3 4a1 1 0 0 1 1-1h3.5a1 1 0 0 1 1 1c0 1.25.2 2.45.57 3.57a1 1 0 0 1-.25 1z"/></svg>
        919-555-0148</p>
      <p class="contact-line">
        <svg class="icon" viewBox="0 0 24 24" fill="none" stroke="#f7dc6f" stroke-width="2"><circle cx="12" cy="12" r="9"/><path d="M3 12h18M12 3c3 3 3 15 0 18M12 3c-3 3-3 15 0 18"/></svg>
        gildedslatworks.com</p>
    </div>
    <div class="appointment-band">Custom Interior &amp; Exterior Window Treatments By Appointment</div>
  </section>
</main>
</body>
</html>
```